Building company buisness cards

We are looking for a sharp modern new look for our business cards.We are a New Zealand based company that specialises in house and land packages.We have attached a photo of the current logo and would like to see if it can be improved somehow if needed.We are open to any colours but we have chosen Black and White at this stage. Feel free to change the font and make the logo smarter looking.Play with the colours and see what looks best.We want a card that looks so good know one will want to throw it away!

Target Market(s)

Building profesonals, home buyers

Industry/Entity Type

Building

Contact Information for Business Card

Garrick Tenwood
0275390628
garrickt@hartvale.co.nz

Font styles to use
Serif
Sans Serif

Colors

Designer to choose colors to be used in the design.

Requirements
Must have
• Just the logo on one side and details on the other
• Clean simple looking card
Nice to have
• Round corners and detail like raised or spot UV
• Something that stands out
Should not have
• To title needed, Director etc

```html
<!DOCTYPE html>
<html lang="en">
<head>
<meta charset="utf-8">
<title>Hartvale Business Cards</title>
<link rel="stylesheet" href="https://fonts.googleapis.com/css2?family=Work+Sans:wght@400;500;700&display=swap">
<style>
  :root {
    --backdrop: #a9a9a9;
    --ink: #111111;
    --paper: #ffffff;
  }
  * { box-sizing: border-box; margin: 0; padding: 0; }
  html, body {
    width: 1200px;
    height: 930px;
    overflow: hidden;
    background: var(--backdrop);
    font-family: "Work Sans", Arial, sans-serif;
  }
  .canvas {
    position: relative;
    width: 1200px;
    height: 930px;
  }
  .card {
    position: absolute;
    width: 520px;
    height: 310px;
    border-radius: 22px;
  }
  .card--front {
    left: 90px;
    top: 100px;
    background: var(--ink);
    color: var(--paper);
    display: flex;
    align-items: center;
    justify-content: center;
  }
  .card--back {
    left: 590px;
    top: 520px;
    background: var(--paper);
    color: var(--ink);
  }
  .wordmark {
    font-weight: 700;
    letter-spacing: -0.5px;
    line-height: 1;
  }
  .card--front .wordmark { font-size: 60px; }
  .card--back .wordmark {
    position: absolute;
    right: 34px;
    top: 32px;
    font-size: 40px;
  }
  .contact {
    position: absolute;
    left: 34px;
    bottom: 30px;
    font-size: 13px;
    letter-spacing: 0.6px;
    line-height: 1.35;
  }
  .contact__name {
    font-size: 17px;
    font-weight: 500;
    letter-spacing: 1.6px;
    text-transform: uppercase;
    margin-bottom: 14px;
  }
  .contact__address { margin-bottom: 12px; }
  .contact__list { list-style: none; }
  .contact__list li {
    display: flex;
    align-items: center;
    gap: 8px;
  }
  .contact__list svg { width: 10px; height: 10px; flex: none; }
</style>
</head>
<body>
<main class="canvas">
  <section class="card card--front" aria-label="Card front">
    <span class="wordmark">Hartvale</span>
  </section>

  <section class="card card--back" aria-label="Card back">
    <span class="wordmark">Hartvale</span>
    <div class="contact">
      <p class="contact__name">Garrick Tenwood</p>
      <p class="contact__address">41b Kerrow Lane,<br>Ashmere, NZ, 7420</p>
      <ul class="contact__list">
        <li>
          <svg viewBox="0 0 10 10" aria-hidden="true"><path d="M2 1 L4 1 L4.5 3 L3.3 3.8 Q4.3 5.8 6.2 6.7 L7 5.5 L9 6 L9 8 Q9 9 8 9 Q2 8.5 1 2 Q1 1 2 1 Z" fill="currentColor"/></svg>
          0275390628
        </li>
        <li>
          <svg viewBox="0 0 10 10" aria-hidden="true"><rect x="0.7" y="2" width="8.6" height="6" fill="none" stroke="currentColor" stroke-width="1.1"/><path d="M0.7 2 L5 5.5 L9.3 2" fill="none" stroke="currentColor" stroke-width="1.1"/></svg>
          garrickt@hartvale.co.nz
        </li>
        <li>
          <svg viewBox="0 0 10 10" aria-hidden="true"><circle cx="5" cy="5" r="4.2" fill="none" stroke="currentColor" stroke-width="1"/><ellipse cx="5" cy="5" rx="1.8" ry="4.2" fill="none" stroke="currentColor" stroke-width="0.9"/><path d="M0.8 5 H9.2" stroke="currentColor" stroke-width="0.9"/></svg>
          www.hartvale.co.nz
        </li>
      </ul>
    </div>
  </section>
</main>
</body>
</html>
```